Request for Business Card Design

Hi. My name is Marlene, I am looking for a new business card design for my company, Quarrow Signal Instruments, LLC. I really like the design you did for Tarsel Venture and was hoping you could do something similar using our full logo and our mark. I am also open to any raised texture design using our mark. I have attached our full logo, which would need to be somewhere on the card, as well as the mark in both outline and full form, as well as our brand colors / guide. The card does not have to be white, as long as our logo and mark appear. I actually like darker colored business cards more, but am open to all options. If you are interested in working with me, please let me know. We would also take the business card design into letterhead design if you can do that.

```html
<!DOCTYPE html>
<html lang="en">
<head>
<meta charset="utf-8">
<title>Quarrow Signal Instruments – Business Card</title>
<link href="https://fonts.googleapis.com/css2?family=Open+Sans:wght@400;600;700;800&display=swap" rel="stylesheet">
<style>
  :root {
    --backdrop: #222223;
    --card: #3e3e40;
    --brand-blue: #1a9bc9;
    --ink-light: #ffffff;
    --ink-soft: #e9e9ea;
  }
  * { box-sizing: border-box; margin: 0; padding: 0; }
  html, body {
    width: 1200px; height: 780px; overflow: hidden;
    background: var(--backdrop);
    font-family: "Open Sans", Arial, sans-serif;
  }
  .stage { position: relative; width: 1200px; height: 780px; }
  .card {
    position: absolute; top: 110px;
    width: 340px; height: 560px;
    background: var(--card);
    border-radius: 28px;
    box-shadow: 0 12px 30px rgba(0,0,0,.55);
    overflow: hidden;
  }
  .card--front { left: 230px; }
  .card--back { left: 630px; }

  /* Front */
  .front-brand__name {
    position: absolute;
    left: 10px; top: 185px;
    width: 320px; height: 80px;
    transform: rotate(-90deg);
    transform-origin: 50% 50%;
    display: flex; flex-direction: column; align-items: flex-start; justify-content: center;
    color: var(--ink-light); font-weight: 700; text-transform: uppercase;
    white-space: nowrap;
  }
  .front-brand__word { font-size: 52px; letter-spacing: 4px; line-height: 1; }
  .front-brand__sub { font-size: 15px; letter-spacing: 1px; line-height: 1; margin-top: 6px; padding-left: 4px; }
  .front-brand__dot {
    position: absolute; left: 127px; top: 402px;
    width: 86px; height: 86px; border-radius: 50%;
    background: var(--brand-blue);
  }

  /* Back */
  .back-brand {
    position: absolute; top: 42px; left: 0; right: 0;
    display: flex; align-items: center; justify-content: center; gap: 12px;
  }
  .back-brand__dot { width: 34px; height: 34px; border-radius: 50%; background: var(--brand-blue); }
  .back-brand__name {
    color: var(--ink-light); font-weight: 700; text-transform: uppercase; line-height: 1.05;
  }
  .back-brand__word { display: block; font-size: 26px; letter-spacing: 3px; }
  .back-brand__sub { display: block; font-size: 9px; letter-spacing: .6px; }

  .person { position: absolute; top: 250px; left: 0; right: 0; text-align: center; }
  .person__name { color: var(--brand-blue); font-weight: 800; font-size: 40px; line-height: 1; }
  .person__role { color: var(--ink-light); font-weight: 600; font-size: 15px; margin-top: 2px; }

  .connectors { position: absolute; left: 0; top: 0; width: 340px; height: 560px; }

  .contact {
    position: absolute; top: 374px; left: 0; right: 0;
    text-align: center; color: var(--ink-soft);
    font-size: 15px; line-height: 22.5px;
  }
  .address {
    position: absolute; top: 508px; left: 0; right: 0;
    text-align: center; color: var(--ink-soft);
    font-size: 15px; line-height: 21px;
  }
</style>
</head>
<body>
<main class="stage">

  <section class="card card--front" aria-label="Card front">
    <div class="front-brand__name">
      <span class="front-brand__word">Quarrow</span>
      <span class="front-brand__sub">Signal Instruments</span>
    </div>
    <span class="front-brand__dot"></span>
  </section>

  <section class="card card--back" aria-label="Card back">
    <div class="back-brand">
      <span class="back-brand__dot"></span>
      <span class="back-brand__name">
        <span class="back-brand__word">Quarrow</span>
        <span class="back-brand__sub">Signal Instruments</span>
      </span>
    </div>

    <div class="person">
      <div class="person__name">Marlene</div>
      <div class="person__role">Director</div>
    </div>

    <svg class="connectors" viewBox="0 0 340 560" aria-hidden="true">
      <g fill="none" stroke="#1a9bc9" stroke-width="1.6">
        <polyline points="97,345 22,345 22,433 44,433"/>
        <polyline points="243,345 318,345 318,456 298,456"/>
        <polyline points="150,358 150,366 60,366 60,387 68,387"/>
        <polyline points="190,358 190,366 288,366 288,409 278,409"/>
      </g>
      <g fill="#1a9bc9">
        <polygon points="52,433 44,428 44,438"/>
        <polygon points="290,456 298,451 298,461"/>
        <polygon points="76,387 68,382 68,392"/>
        <polygon points="270,409 278,404 278,414"/>
      </g>
      <g fill="#1a9bc9">
        <circle cx="110" cy="345" r="13"/>
        <circle cx="150" cy="345" r="13"/>
        <circle cx="190" cy="345" r="13"/>
        <circle cx="230" cy="345" r="13"/>
        <circle cx="170" cy="486" r="12"/>
      </g>
      <g fill="none" stroke="#ffffff" stroke-width="1.4" stroke-linejoin="round" stroke-linecap="round">
        <rect x="103" y="340" width="14" height="10" rx="1"/>
        <polyline points="103,341 110,346 117,341"/>
        <path d="M145 340 q-2 2 0 5 q3 4 7 6 q3 1 4 -1 l-2 -2 l-2 1 q-3 -2 -4 -4 l1 -2 z"/>
        <rect x="183" y="343" width="14" height="8" rx="1"/>
        <rect x="186" y="338" width="8" height="5"/>
        <line x1="186" y1="347" x2="194" y2="347"/>
        <circle cx="230" cy="345" r="7"/>
        <ellipse cx="230" cy="345" rx="3" ry="7"/>
        <line x1="223" y1="345" x2="237" y2="345"/>
        <path d="M170 493 c-4 -5 -6 -7 -6 -10 a6 6 0 0 1 12 0 c0 3 -2 5 -6 10 z"/>
        <circle cx="170" cy="483" r="2"/>
      </g>
    </svg>

    <div class="contact">
      <div>+001 555 210 4831</div>
      <div>+001 555 210 4832</div>
      <div>info@quarrowsignal.com</div>
      <div>www.quarrowsignal.com</div>
    </div>

    <div class="address">
      <div>1180 Halden Park Road •</div>
      <div>Fernvale, CO 80999</div>
    </div>
  </section>

</main>
</body>
</html>
```